Alapca breeding needs a website

Presentation of the farm, animals (stallions, mares, information about the animals, for sale) and possible later expansion with a webshop (alpaca wool products). We want to present our farm and the animals on the farm on this page. A mission why we are doing this. Furthermore, each animal should be shown with a picture and described. Later we want to sell our own products made from alpaca wool via a webshop. But we still need to grow a bit to do that.

Target Market(s)

Information about my alpaca breeding and the alpaca farm

Industry/Entity Type

Tierzucht

Number of Pages Required

1 page

Font styles to use
Sans Serif

Requirements
Must have
• Modern design that matches the logo
Nice to have
• Intuitive operation / Clear structure
Should not have
• No

```html
<!DOCTYPE html>
<html lang="en">
<head>
<meta charset="utf-8">
<title>Verdant Alpacas</title>
<link href="https://fonts.googleapis.com/css2?family=Cinzel:wght@400;600;700&family=Lato:wght@400;700&display=swap" rel="stylesheet">
<style>
:root{
  --navy:#0c1f3f;
  --green:#8cc63f;
  --green-dark:#74ab2c;
  --lavender:#f3f2fa;
  --white:#ffffff;
  --text:#333a45;
}
*{margin:0;padding:0;box-sizing:border-box}
html,body{width:1200px;height:3603px;overflow:hidden}
body{position:relative;background:var(--white);font-family:'Lato',sans-serif;color:var(--text)}
.abs{position:absolute}
.serif{font-family:'Cinzel',serif}
.btn{position:absolute;display:flex;align-items:center;justify-content:center;font-family:'Cinzel',serif;font-weight:700;font-size:17px;letter-spacing:.5px;border-radius:10px 0 10px 0;box-shadow:4px 4px 0 rgba(0,0,0,.12)}
.btn-green{background:var(--green);color:var(--navy)}
.btn-navy{background:var(--navy);color:var(--green)}

/* header */
.topbar{top:0;left:0;width:1200px;height:102px;background:var(--white)}
.brand-disc{top:-40px;left:75px;width:200px;height:200px;border-radius:50%;background:var(--white);box-shadow:0 4px 0 #c8cdd6;z-index:3}
.brand-name{top:92px;left:75px;width:200px;text-align:center;font-family:'Cinzel',serif;font-weight:700;font-size:26px;color:var(--navy);z-index:4;line-height:1}
.mail{top:28px;left:558px;display:flex;gap:12px;align-items:center}
.mail-label{font-family:'Cinzel',serif;font-size:11px;color:var(--navy)}
.mail-value{font-family:'Cinzel',serif;font-size:15px;color:var(--navy)}
.cart{top:36px;left:826px}
.navbar{top:102px;left:0;width:1200px;height:64px;background:var(--navy)}
.nav{position:absolute;top:125px;left:317px;display:flex;gap:34px;font-family:'Cinzel',serif;font-size:15px;color:var(--white)}
.call{top:102px;left:953px;width:247px;height:64px;background:var(--green)}
.call-icon{top:112px;left:932px;width:40px;height:40px;border-radius:50%;background:var(--white);border:3px solid var(--navy);display:flex;align-items:center;justify-content:center}
.call-text{top:112px;left:982px;font-family:'Cinzel',serif;color:var(--navy)}

/* hero */
.hero{top:166px;left:0;width:1200px;height:580px;background:linear-gradient(180deg,#9fb6c9 0%,#c9d3d4 30%,#8aa84a 55%,#6e9a32 100%)}
.hero-title{top:220px;left:0;width:1200px;text-align:center;color:var(--white);font-family:'Cinzel',serif;text-shadow:0 2px 4px rgba(0,0,0,.45)}
.hero-title .small{font-size:34px;font-weight:700;display:block}
.hero-title .big{font-size:68px;font-weight:700;display:block;margin-top:8px}

/* section heads */
.emblem{width:40px;height:40px;border-radius:50%;border:3px solid var(--navy);position:absolute}
.emblem::after{content:"";position:absolute;inset:8px;border-radius:50%;background:var(--green)}
.sec-title{position:absolute;left:0;width:1200px;text-align:center;font-family:'Cinzel',serif;font-weight:700;font-size:38px;color:var(--navy)}
.sec-sub{position:absolute;left:0;width:1200px;text-align:center;font-family:'Cinzel',serif;font-size:17px;letter-spacing:2px;color:var(--green)}
.sec-sub::before,.sec-sub::after{content:"";display:inline-block;width:26px;height:1px;background:var(--green);vertical-align:middle;margin:0 8px}

/* cards */
.card{position:absolute;top:884px;width:292px;height:358px;border-radius:14px;padding:12px;box-shadow:0 0 0 3px #fff,0 4px 14px rgba(0,0,0,.18);overflow:hidden}
.card-navy{background:var(--navy)}
.card-green{background:var(--green)}
.card-photo{width:268px;height:232px;border-radius:10px 10px 70% 0/10px 10px 40% 0;position:relative}
.sale{position:absolute;top:12px;right:14px;background:#fff;color:#222;font-size:12px;padding:2px 6px;border-radius:4px}
.card h3{font-family:'Cinzel',serif;font-weight:700;font-size:19px;color:#fff;text-align:center;margin-top:20px}
.card p{font-size:11.5px;line-height:24px;color:#fff;text-align:center;margin-top:6px}

/* mission */
.mission{top:1318px;left:0;width:1200px;height:529px;background:var(--green)}
.mission-copy{top:1440px;left:110px;width:500px;color:#fff}
.mission-copy h2{font-family:'Cinzel',serif;font-weight:700;font-size:38px}
.mission-copy .about{font-family:'Cinzel',serif;font-size:17px;letter-spacing:2px;margin-top:10px;margin-left:2px}
.mission-copy .about::after{content:"";display:inline-block;width:24px;height:1px;background:#fff;vertical-align:middle;margin-left:12px}
.mission-copy p{font-size:15px;line-height:26px;margin-top:18px;text-align:justify}
.mission-art{top:1385px;left:675px;width:415px;height:400px;border-radius:50% 50% 12px 12px;background:radial-gradient(circle at 50% 60%,var(--navy) 0 45%,#a9d468 46% 100%)}

/* products */
.product-frame{top:2095px;left:112px;width:418px;height:348px;background:#fff;box-shadow:0 2px 14px rgba(0,0,0,.15);border-radius:6px;padding:13px}
.product-photo{width:100%;height:100%;background:linear-gradient(135deg,#8a6b52,#e9dfcf 45%,#d8cbb6)}
.product-copy{top:2090px;left:598px;width:480px}
.product-copy h3{font-family:'Cinzel',serif;font-weight:700;font-size:28px;color:var(--navy)}
.stars{color:#f5b800;font-size:18px;letter-spacing:1px;margin-top:6px}
.product-copy p{font-size:14.5px;line-height:29px;color:var(--text);margin-top:12px}
.product-copy p+p{margin-top:29px}
.thumb{position:absolute;top:2502px;width:149px;height:111px;border:1px solid #ddd}
.arrow{position:absolute;top:2545px;width:24px;height:24px;border-radius:50%;background:#333;display:flex;align-items:center;justify-content:center}

/* newsletter */
.newsletter{top:2700px;left:0;width:1200px;height:420px;background:var(--lavender)}
.email-field{top:2921px;left:148px;width:902px;height:69px;background:#fff;border-radius:35px;box-shadow:0 2px 10px rgba(0,0,0,.08);display:flex;align-items:center;padding-left:25px;font-size:14px;font-weight:700;color:var(--navy)}

/* footer */
.footer{top:3150px;left:0;width:1200px;height:453px;background:var(--navy)}
.foot-brand{top:3300px;left:140px;width:210px;text-align:center;color:#fff}
.foot-brand .disc{width:110px;height:110px;border-radius:50%;border:3px solid var(--green);margin:0 auto 16px}
.foot-brand .name{font-family:'Cinzel',serif;font-weight:700;font-size:34px;line-height:1}
.foot-col{top:3264px;color:#fff}
.foot-col h4{font-family:'Cinzel',serif;font-weight:400;font-size:19px;margin-bottom:14px;letter-spacing:.5px}
.foot-col li{list-style:none;font-size:15px;line-height:34px;display:flex;align-items:center;gap:10px}
.contact-row{display:flex;gap:14px;align-items:flex-start;font-size:15px;line-height:27px;margin-bottom:16px}
.contact-row .ic{width:30px;height:30px;border-radius:50%;background:#fff;flex:none;display:flex;align-items:center;justify-content:center}
.divider{top:3512px;left:112px;width:976px;height:1px;background:#8d98ab}
.copyright{top:3553px;left:0;width:1200px;text-align:center;color:#fff;font-weight:700;font-size:15px}
</style>
</head>
<body>

<!-- header -->
<div class="abs topbar"></div>
<div class="abs navbar"></div>
<div class="abs call"></div>
<div class="abs brand-disc"></div>
<div class="abs brand-name">VERDANT</div>

<div class="abs mail">
  <svg width="34" height="30" viewBox="0 0 34 30"><rect x="2" y="8" width="30" height="20" fill="none" stroke="#8cc63f" stroke-width="2"/><path d="M2 8 L17 20 L32 8" fill="none" stroke="#8cc63f" stroke-width="2"/><circle cx="17" cy="9" r="5" fill="none" stroke="#8cc63f" stroke-width="1.5"/></svg>
  <div><div class="mail-label">SEND US EMAIL</div><div class="mail-value">info@verdantalpacas.com</div></div>
</div>
<div class="abs cart">
  <svg width="30" height="28" viewBox="0 0 30 28"><path d="M2 3 H7 L10 18 H24 L27 7 H8" fill="none" stroke="#0c1f3f" stroke-width="3" stroke-linejoin="round"/><circle cx="12" cy="23" r="2.5" fill="#0c1f3f"/><circle cx="22" cy="23" r="2.5" fill="#0c1f3f"/><circle cx="25" cy="5" r="5" fill="#8cc63f"/><text x="25" y="8" font-size="8" text-anchor="middle" fill="#0c1f3f" font-family="Lato,sans-serif">0</text></svg>
</div>
<div class="btn btn-green" style="top:27px;left:912px;width:176px;height:42px;font-size:14px">REQUEST A QUOTE</div>

<nav class="nav"><span>HOME</span><span>MISSION</span><span>PRODUCTS</span><span>ANIMALS FARM</span><span>CONTACT US</span></nav>
<div class="abs call-icon"><svg width="18" height="18" viewBox="0 0 24 24"><path d="M6.6 10.8a15 15 0 006.6 6.6l2.2-2.2c.3-.3.7-.4 1-.2 1.1.4 2.3.6 3.6.6.6 0 1 .4 1 1V20c0 .6-.4 1-1 1A17 17 0 013 4c0-.6.4-1 1-1h3.5c.6 0 1 .4 1 1 0 1.3.2 2.5.6 3.6.1.3 0 .7-.2 1z" fill="none" stroke="#0c1f3f" stroke-width="1.6"/></svg></div>
<div class="abs call-text"><div style="font-size:11px">CALL US</div><div style="font-size:16px">+1 555 010 2040</div></div>

<!-- hero -->
<div class="abs hero" role="img" aria-label="Photo of alpacas grazing in a green meadow with mountains behind"></div>
<div class="abs hero-title"><span class="small">WELCOME TO</span><span class="big">VERDANT ALPACA</span></div>
<div class="btn btn-green" style="top:368px;left:522px;width:158px;height:50px">GET STARTED</div>
<svg class="abs" style="top:600px;left:0" width="1200" height="146" viewBox="0 0 1200 146">
  <path d="M0 146 L0 140 Q600 -10 1200 140 L1200 146 Z" fill="#fff"/>
  <path d="M80 126 Q600 20 1120 126 Q600 60 80 126 Z" fill="#0c1f3f"/>
  <circle cx="600" cy="55" r="42" fill="#fff"/>
  <circle cx="600" cy="55" r="22" fill="none" stroke="#0c1f3f" stroke-width="3"/>
  <circle cx="600" cy="55" r="12" fill="#8cc63f"/>
</svg>

<!-- animals farm -->
<div class="emblem" style="top:726px;left:580px"></div>
<div class="sec-title" style="top:776px">ANIMALS FARM</div>
<div class="sec-sub" style="top:832px">ALPACAS</div>

<div class="card card-navy" style="left:112px">
  <div class="card-photo" role="img" aria-label="Photo of a dark stallion galloping at sunset" style="background:linear-gradient(160deg,#f0b050,#a0601c 55%,#3a2210)"><span class="sale">SALE</span></div>
  <h3>STALLIONS</h3>
  <p>Temporibus autem quibusdam et aut officiis debitis aut rerum necessitatibus</p>
</div>
<div class="card card-green" style="left:455px">
  <div class="card-photo" role="img" aria-label="Photo of a herd of brown mares running" style="background:linear-gradient(170deg,#8aa3c0,#c8b79a 45%,#7a4a26)"></div>
  <h3>MARES</h3>
  <p>Temporibus autem quibusdam et aut officiis debitis aut rerum necessitatibus</p>
</div>
<div class="card card-navy" style="left:798px">
  <div class="card-photo" role="img" aria-label="Photo of alpacas standing on a farm" style="background:linear-gradient(170deg,#9cc0e6,#e8ece8 45%,#6e8e3a)"><span class="sale">SALE</span></div>
  <h3>ALPACA WOOL</h3>
  <p>Temporibus autem quibusdam et aut officiis debitis aut rerum necessitatibus</p>
</div>

<!-- mission -->
<div class="abs mission"></div>
<div class="emblem" style="top:1385px;left:113px;border-color:#fff"></div>
<div class="abs mission-copy">
  <h2>OUR MISSION</h2>
  <div class="about">ABOUT</div>
  <p style="text-align:left">Nam libero tempore, cum soluta nobis est eligendi optio cumque nihil cere menda est, omnis dolor repellendus. Temporibus autem quibusdam et aut rum eveniet uepudiandae sint et molestiae non recusandae.</p>
  <p style="margin-top:26px">Itaque earum rerum hic tenetur a sapiente delectus, ut aut reiciendis voluptatibus maiores alias consequatur aut perferendis doloribus asperiores repellat.</p>
</div>
<div class="btn btn-navy" style="top:1737px;left:112px;width:158px;height:50px">READ MORE</div>
<div class="abs mission-art" role="img" aria-label="Illustration of two alpacas beneath a leafy tree"></div>

<!-- products -->
<div class="emblem" style="top:1912px;left:580px"></div>
<div class="sec-title" style="top:1964px">OUR OWN PRODUCTS</div>
<div class="sec-sub" style="top:2020px">PRODUCTS</div>

<div class="abs product-frame"><div class="product-photo" role="img" aria-label="Photo of hands holding raw alpaca wool"></div></div>
<div class="abs product-copy">
  <h3>ALPACA WOOL</h3>
  <div class="stars">★★★★★</div>
  <p>Temporibus autem quibusdam et aut officiis debitis aut rerum necessita tibus saepe eveniet ut et voluptates repudiandae sint et molestiae non recusandae.</p>
  <p>Itaque earum rerum hic tenetur a sapiente delectus, ut aut reiciendis voluptatibus maiores alias consequatur aut perferendis doloribus asperiores repellat.</p>
</div>
<div class="btn btn-green" style="top:2387px;left:600px;width:158px;height:50px">READ MORE</div>

<div class="arrow" style="left:39px"><svg width="10" height="10" viewBox="0 0 10 10"><path d="M7 1 L3 5 L7 9" fill="none" stroke="#fff" stroke-width="2"/></svg></div>
<div class="thumb" role="img" aria-label="Photo of hands sorting fleece" style="left:112px;background:linear-gradient(135deg,#6b4c36,#d9cbb4)"></div>
<div class="thumb" role="img" aria-label="Photo of raw wool pile" style="left:317px;background:linear-gradient(135deg,#a58b6e,#efe6d6)"></div>
<div class="thumb" role="img" aria-label="Photo of spun wool skeins" style="left:524px;background:linear-gradient(135deg,#e8dccb,#f2d7d6)"></div>
<div class="thumb" role="img" aria-label="Photo of colored fleece samples" style="left:731px;background:linear-gradient(135deg,#7b6a72,#e8e8ee 50%,#a0603c)"></div>
<div class="thumb" role="img" aria-label="Photo of a hand on knitted alpaca fabric" style="left:939px;background:linear-gradient(135deg,#d9c9b0,#f1e9dc)"></div>
<div class="arrow" style="left:1120px"><svg width="10" height="10" viewBox="0 0 10 10"><path d="M3 1 L7 5 L3 9" fill="none" stroke="#fff" stroke-width="2"/></svg></div>

<!-- newsletter -->
<div class="abs newsletter"></div>
<div class="emblem" style="top:2762px;left:578px"></div>
<div class="sec-title" style="top:2813px">SIGNUP OUR NEWSLETTER</div>
<div class="sec-sub" style="top:2870px">NEWSLETTER</div>
<div class="abs email-field">Enter the email</div>
<div class="btn btn-green" style="top:3028px;left:520px;width:158px;height:50px">SUBSCRIBE</div>

<!-- footer -->
<div class="abs footer"></div>
<svg class="abs" style="top:3070px;left:0" width="1200" height="120" viewBox="0 0 1200 120">
  <rect width="1200" height="120" fill="#0c1f3f"/>
  <path d="M0 0 H1200 V20 Q600 150 0 20 Z" fill="#f3f2fa"/>
  <path d="M80 50 Q600 170 1120 50 Q600 140 80 50 Z" fill="#fff"/>
</svg>

<div class="abs foot-brand">
  <div class="disc"></div>
  <div class="name">VERDANT</div>
</div>

<div class="abs foot-col" style="left:432px">
  <h4>QUICK LINKS</h4>
  <ul>
    <li><span>➜</span>Home</li><li><span>➜</span>Mission</li><li><span>➜</span>Animal Farm</li><li><span>➜</span>Products</li><li><span>➜</span>Contact Us</li>
  </ul>
</div>
<div class="abs foot-col" style="left:664px">
  <h4>HELP LINKS</h4>
  <ul>
    <li><span>➜</span>FAQ</li><li><span>➜</span>Terms of use</li><li><span>➜</span>Privacy Policy</li><li><span>➜</span>Support Links</li><li><span>➜</span>Conditions</li>
  </ul>
</div>
<div class="abs foot-col" style="left:887px">
  <h4>CONTACT US</h4>
  <div class="contact-row"><span class="ic"><svg width="14" height="16" viewBox="0 0 14 16"><path d="M7 0a6 6 0 00-6 6c0 4.5 6 10 6 10s6-5.5 6-10a6 6 0 00-6-6z" fill="#0c1f3f"/><circle cx="7" cy="6" r="2" fill="#fff"/></svg></span><span>Verdant Alpaca<br>United States</span></div>
  <div class="contact-row"><span class="ic"><svg width="14" height="14" viewBox="0 0 24 24"><path d="M6.6 10.8a15 15 0 006.6 6.6l2.2-2.2c.3-.3.7-.4 1-.2 1.1.4 2.3.6 3.6.6.6 0 1 .4 1 1V20c0 .6-.4 1-1 1A17 17 0 013 4c0-.6.4-1 1-1h3.5c.6 0 1 .4 1 1 0 1.3.2 2.5.6 3.6.1.3 0 .7-.2 1z" fill="#0c1f3f"/></svg></span><span style="line-height:30px">+1 555 010 2040</span></div>
  <div class="contact-row"><span class="ic"><svg width="14" height="12" viewBox="0 0 14 12"><rect width="14" height="12" rx="2" fill="#0c1f3f"/><path d="M1 2 L7 7 L13 2" fill="none" stroke="#fff" stroke-width="1.5"/></svg></span><span style="line-height:30px">info@verdantalpaca.com</span></div>
</div>

<div class="abs divider"></div>
<div class="abs copyright">Copyrights@2024.Verdant Alpaca.All Rights Reserved</div>

</body>
</html>
```